Business card for medical clinic

I need an upmarket, modern medical/health business card for my clinic

Contact Information for Business Card

name, address, email, qr code

```html
<!DOCTYPE html>
<html lang="en">
<head>
<meta charset="utf-8">
<title>Meridell Health Partners – Business Card</title>
<link rel="stylesheet" href="https://fonts.googleapis.com/css2?family=Montserrat:wght@400;500;700&display=swap">
<style>
  :root {
    --stage: #1c1c1e;
    --paper: #ffffff;
    --navy: #1e2844;
    --ink: #1b2440;
    --brand-blue: #1b6fa3;
    --sky: #29abe2;
    --emboss: #34468f;
  }
  * { margin: 0; padding: 0; box-sizing: border-box; }
  html, body { width: 1200px; height: 1059px; overflow: hidden; }
  body {
    background: var(--stage);
    font-family: "Montserrat", Arial, sans-serif;
    position: relative;
  }
  .card { position: absolute; overflow: hidden; }

  /* Front */
  .card--front {
    left: 256px; top: 89px; width: 688px; height: 391px;
    background: var(--paper);
  }
  .brand {
    position: absolute; left: 18px; top: 62px;
    display: flex; align-items: center; gap: 14px;
  }
  .brand__ring {
    width: 46px; height: 46px; border-radius: 50%;
    border: 4px solid var(--brand-blue);
  }
  .brand__name {
    font-weight: 500; font-size: 30px; letter-spacing: 1px;
    color: var(--brand-blue); text-transform: uppercase;
  }
  .accent-bar {
    position: absolute; left: 0; top: 227px; width: 14px; height: 41px;
    background: var(--sky);
  }
  .person { position: absolute; left: 34px; top: 218px; color: var(--ink); }
  .person__name { font-weight: 700; font-size: 24px; line-height: 1.2; }
  .person__title { font-weight: 400; font-size: 14px; margin-top: 2px; }
  .divider {
    position: absolute; left: 33px; top: 270px; width: 614px; height: 1px;
    background: var(--sky);
  }
  .contacts {
    position: absolute; left: 36px; top: 285px; list-style: none;
    color: var(--ink); font-size: 14.5px;
  }
  .contacts li { display: flex; align-items: center; height: 27.5px; }
  .contacts svg { width: 15px; height: 15px; margin-right: 10px; fill: var(--ink); }
  .address {
    position: absolute; right: 41px; top: 410px; top: 321px;
    text-align: right; color: var(--ink); font-size: 15px; line-height: 18px;
    font-style: normal;
  }
  .footer-band { position: absolute; left: 0; bottom: 0; width: 688px; height: 21px; }

  /* Back */
  .card--back {
    left: 253px; top: 546px; width: 695px; height: 395px;
    background: var(--navy);
  }
  .back-brand {
    position: absolute; left: 0; right: 0; top: 0; bottom: 0;
    display: flex; align-items: center; justify-content: center; gap: 16px;
  }
  .back-brand__ring {
    width: 56px; height: 56px; border-radius: 50%;
    border: 4px solid var(--emboss);
  }
  .back-brand__name {
    font-weight: 500; font-size: 34px; letter-spacing: 1px;
    color: var(--emboss); text-transform: uppercase;
  }
</style>
</head>
<body>
  <section class="card card--front">
    <div class="brand">
      <span class="brand__ring"></span>
      <span class="brand__name">Meridell Health Partners</span>
    </div>

    <span class="accent-bar"></span>
    <div class="person">
      <h1 class="person__name">Daniel Brooks</h1>
      <p class="person__title">Managing Director</p>
    </div>
    <span class="divider"></span>

    <ul class="contacts">
      <li>
        <svg viewBox="0 0 24 24" aria-hidden="true"><path d="M6.6 10.8a15.1 15.1 0 0 0 6.6 6.6l2.2-2.2c.3-.3.7-.4 1-.2 1.1.4 2.3.6 3.6.6.6 0 1 .4 1 1V20c0 .6-.4 1-1 1A17 17 0 0 1 3 4c0-.6.4-1 1-1h3.5c.6 0 1 .4 1 1 0 1.3.2 2.5.6 3.6.1.3 0 .7-.2 1z"/></svg>
        555.210.4470
      </li>
      <li>
        <svg viewBox="0 0 24 24" aria-hidden="true"><path d="M2 5h20v14H2z M2 5l10 7 10-7" fill="var(--ink)"/><path d="M2 6l10 7 10-7" fill="none" stroke="#fff" stroke-width="1.5"/></svg>
        hello@meridellhealth.com
      </li>
      <li>
        <svg viewBox="0 0 24 24" aria-hidden="true"><circle cx="12" cy="12" r="10"/><path d="M12 2a15 15 0 0 1 0 20M12 2a15 15 0 0 0 0 20M2 12h20" fill="none" stroke="#fff" stroke-width="1.4"/></svg>
        www.meridellhealth.com
      </li>
    </ul>

    <address class="address">42 Cedar Hollow Lane<br>Fairview, TN 37062</address>

    <svg class="footer-band" viewBox="0 0 688 21" aria-hidden="true">
      <polygon points="0,0 356,0 326,21 0,21" fill="var(--navy)"/>
      <polygon points="368,0 688,0 688,21 338,21" fill="var(--sky)"/>
    </svg>
  </section>

  <section class="card card--back">
    <div class="back-brand">
      <span class="back-brand__ring"></span>
      <span class="back-brand__name">Meridell Health Partners</span>
    </div>
  </section>
</body>
</html>
```